Popup Nightclub Grand Opening Flyer

We need to design a flyer for the grand opening of an upscale, exclusive nightclub called "Lantern". The design needs to be chic and exclusive. The background should be black and the text should primarily be white. We like minimalist designs.

Here is the text for the flyer
-
Velvetroll Atlanta Presents

Lantern (LOGO)

A Popup Nightclub Experience
For one night Only

Friday, October 18, 2013
Party begins at 9PM

INVITE ONLY

See invitation for location details
(Velvetroll Atlanta logo)

-
Examples we like

http://cdn4-x.pressfolio-example.com/sites/default/files/styles/image_content_width/hash/3b/fd/2468013579_4421_flyer.jpg?itok=K9rtQw2z

http://files.hubspace-example.net/files/8Hqq-Tr72WWE3kaRbTmcxP5QZK2F396J8nbRw4CKMHfdX2Y7qSEF-MqjxDoNrLY3QCyQJD7npjGaRq3k-Mhx6hqf3MDSWf8r3/2zenSaturdays.jpg

http://morvex-example.com/wp-content/uploads/siteskin/widgetkit/gallery/2zen/2zen-gen_qstay4-01.jpg

Hi All, one thing that we are seeing that we don't like is on over emphasis on the phrase "a popup nightclub experience" please don't make this the largest thing on the flyer

Target Market(s)

Target market is 25-35 year olds who are affluent (rich) and like luxury brands

Requirements
Must have
• Dark Background
Nice to have
• Velvetroll Logo on the bottom
Modern text that isn't curvy
Should not have
• Curved text

```html
<!DOCTYPE html>
<html lang="en">
<head>
<meta charset="utf-8">
<title>Lantern Nightclub – Popup Flyer</title>
<link rel="stylesheet" href="https://fonts.googleapis.com/css2?family=Questrial&family=Roboto+Condensed:wght@300;700&family=Barlow:wght@400&display=swap">
<style>
  :root {
    --ink: #000000;
    --white: #ffffff;
    --silver-light: #f2f2f2;
    --silver-mid: #b9b9b9;
    --silver-dark: #8a8a8a;
    --grey-text: #a8a8a8;
    --glow: #3a332e;
  }
  html, body {
    margin: 0;
    padding: 0;
    width: 867px;
    height: 1200px;
    overflow: hidden;
    background: var(--ink);
  }
  .flyer {
    position: relative;
    width: 867px;
    height: 1200px;
    background: var(--ink);
    color: var(--white);
    overflow: hidden;
    text-align: center;
  }
  .flyer p, .flyer h1 { margin: 0; }
  .ornament-field {
    position: absolute;
    inset: 0;
    background:
      radial-gradient(ellipse 190px 160px at 50% 52%, var(--glow) 0%, rgba(40,34,30,0.45) 55%, transparent 100%),
      radial-gradient(ellipse 330px 260px at 50% 24%, rgba(42,36,32,0.55) 0%, transparent 70%),
      radial-gradient(ellipse 360px 240px at 50% 88%, rgba(42,36,32,0.45) 0%, transparent 70%);
  }
  .presenter {
    position: absolute;
    top: 90px;
    left: 0;
    right: 0;
    font-family: "Questrial", sans-serif;
    font-size: 31px;
    line-height: 1;
  }
  .presents {
    position: absolute;
    top: 136px;
    left: 0;
    right: 0;
    font-family: "Questrial", sans-serif;
    font-size: 22px;
    letter-spacing: 7px;
    line-height: 1;
  }
  .venue-mark {
    position: absolute;
    top: 196px;
    left: 50%;
    transform: translateX(-50%);
  }
  .venue-name {
    position: absolute;
    top: 326px;
    left: 0;
    right: 0;
    font-family: "Questrial", sans-serif;
    font-size: 60px;
    letter-spacing: 10px;
    line-height: 1;
    padding-left: 10px;
  }
  .venue-type {
    position: absolute;
    top: 400px;
    left: 0;
    right: 0;
    font-family: "Questrial", sans-serif;
    font-size: 20px;
    letter-spacing: 3px;
    line-height: 1;
  }
  .rule-sparkle {
    position: absolute;
    left: 277px;
    width: 300px;
    height: 2px;
    background: linear-gradient(90deg, transparent 0%, var(--silver-mid) 15%, var(--white) 50%, var(--silver-mid) 85%, transparent 100%);
  }
  .rule-top { top: 500px; }
  .rule-bottom { top: 780px; }
  .headline {
    position: absolute;
    top: 520px;
    left: 0;
    right: 0;
    font-family: "Roboto Condensed", sans-serif;
    font-weight: 700;
    font-size: 50px;
    line-height: 62px;
    background: linear-gradient(180deg, var(--silver-light) 0%, var(--silver-mid) 55%, var(--silver-dark) 100%);
    -webkit-background-clip: text;
    background-clip: text;
    color: transparent;
  }
  .headline span { display: block; }
  .tagline {
    position: absolute;
    top: 722px;
    left: 0;
    right: 0;
    font-family: "Barlow", sans-serif;
    font-size: 28px;
    line-height: 1;
    color: var(--silver-light);
  }
  .event-details {
    position: absolute;
    top: 850px;
    left: 233px;
    width: 400px;
    padding: 10px 0 8px;
    border-top: 2px dotted var(--silver-mid);
    border-bottom: 2px dotted var(--silver-mid);
    font-family: "Roboto Condensed", sans-serif;
    font-size: 30px;
    line-height: 1.1;
    white-space: nowrap;
  }
  .event-date { font-weight: 700; }
  .event-time { font-weight: 300; }
  .access-note {
    position: absolute;
    top: 968px;
    left: 0;
    right: 0;
    font-family: "Roboto Condensed", sans-serif;
    font-weight: 700;
    font-size: 20px;
    letter-spacing: 6px;
    padding-left: 6px;
    line-height: 1;
    color: var(--silver-light);
  }
  .location-note {
    position: absolute;
    top: 1020px;
    left: 0;
    right: 0;
    font-family: "Barlow", sans-serif;
    font-size: 16px;
    letter-spacing: 0.5px;
    line-height: 1;
    color: var(--grey-text);
  }
  .host-sign {
    position: absolute;
    top: 1060px;
    left: 0;
    right: 0;
    display: flex;
    justify-content: center;
    align-items: center;
    gap: 12px;
  }
  .host-dot {
    width: 24px;
    height: 24px;
    border-radius: 50%;
    background: var(--silver-mid);
  }
  .host-name {
    font-family: "Questrial", sans-serif;
    font-size: 24px;
    letter-spacing: 4px;
    line-height: 1;
    color: var(--white);
  }
</style>
</head>
<body>
  <main class="flyer">
    <div class="ornament-field" role="img" aria-label="Faint dark brown symmetrical petal ornament pattern glowing softly behind the text"></div>

    <p class="presenter">Velvetroll Atlanta</p>
    <p class="presents">Presents</p>

    <svg class="venue-mark" width="96" height="96" viewBox="0 0 96 96" aria-hidden="true">
      <circle cx="48" cy="48" r="44" fill="none" stroke="#c9c9c9" stroke-width="6"/>
    </svg>

    <p class="venue-name">LANTERN</p>
    <p class="venue-type">NIGHTCLUB</p>

    <div class="rule-sparkle rule-top"></div>
    <h1 class="headline">
      <span>A POPUP</span>
      <span>NIGHTCLUB</span>
      <span>EXPERIENCE</span>
    </h1>
    <p class="tagline">For one night only</p>
    <div class="rule-sparkle rule-bottom"></div>

    <div class="event-details">
      <div class="event-date">FRIDAY, OCTOBER 18, 2013</div>
      <div class="event-time">PARTY BEGINS AT 9PM</div>
    </div>

    <p class="access-note">INVITE ONLY</p>

    <p class="location-note">See invitation for location details</p>

    <div class="host-sign">
      <span class="host-dot"></span>
      <span class="host-name">VELVETROLL ATLANTA</span>
    </div>
  </main>
</body>
</html>
```